New Business Card Design Project

Use the flyer uploaded and website www.brightoakbuilders.com for inspiration.
List Our Services on Backside of business cards
Marcus Delling
Harborline Builders Inc.
Licensed General Contractors
858-471-6093

Contact Information for Business Card

Use the flyer uploaded and website www.brightoakbuilders.com for inspiration. List Our Services on Backside of business cards Marcus Delling Harborline Builders Inc. Licensed General Contractors 858-471-6093

```html
<!DOCTYPE html>
<html lang="en">
<head>
<meta charset="utf-8">
<title>Harborline Builders – Business Cards</title>
<link rel="stylesheet" href="https://fonts.googleapis.com/css2?family=Roboto:wght@400;500;700;900&display=swap">
<style>
  :root {
    --page: #232323;
    --card: #1e1f24;
    --edge: #e8212a;
    --red: #ed1c24;
    --blue: #5685c9;
    --ink: #ffffff;
    --muted: #d9d9de;
  }
  * { box-sizing: border-box; margin: 0; padding: 0; }
  html, body { width: 1200px; height: 780px; overflow: hidden; }
  body {
    background: var(--page);
    font-family: "Roboto", Arial, sans-serif;
    color: var(--ink);
    position: relative;
  }
  .card {
    position: absolute;
    top: 230px;
    width: 560px;
    height: 320px;
    background: var(--card);
    border-radius: 22px;
    border-bottom: 4px solid var(--edge);
    border-left: 2px solid var(--edge);
    overflow: hidden;
  }
  .card--back { left: 27px; }
  .card--front { left: 613px; }

  .brand {
    display: flex;
    align-items: center;
    gap: 10px;
    font-size: 26px;
    font-weight: 400;
    letter-spacing: 2px;
    text-transform: uppercase;
    color: var(--ink);
    white-space: nowrap;
  }
  .brand__dot {
    width: 12px; height: 12px;
    border-radius: 50%;
    background: var(--ink);
    flex: none;
  }

  /* back side */
  .card--back .brand { position: absolute; top: 70px; left: 0; right: 0; justify-content: center; }
  .guarantee {
    position: absolute; top: 150px; left: 0; right: 0;
    text-align: center;
    font-weight: 900; font-size: 15px; color: var(--red);
  }
  .specialty {
    position: absolute; top: 172px; left: 0; right: 0;
    display: flex; align-items: center; justify-content: center; gap: 12px;
    font-weight: 900; font-size: 13px; color: var(--blue);
  }
  .specialty__rule { height: 2px; width: 150px; background: var(--blue); }
  .services {
    position: absolute; top: 204px; left: 22px; right: 22px;
    list-style: none;
    display: flex; flex-wrap: wrap; justify-content: center;
    column-gap: 10px; row-gap: 7px;
    font-size: 11.5px; font-weight: 500; color: var(--ink);
  }
  .services li { display: flex; align-items: center; gap: 4px; white-space: nowrap; }
  .tick { width: 10px; height: 10px; flex: none; }

  /* front side */
  .card--front .brand {
    position: absolute; top: 140px; left: 14px; width: 234px;
    justify-content: center;
    font-size: 15px; letter-spacing: 1.5px; gap: 8px;
  }
  .card--front .brand__dot { width: 9px; height: 9px; }
  .divider {
    position: absolute; left: 262px; top: 40px;
    width: 2px; height: 178px; background: var(--blue);
  }
  .contact { position: absolute; left: 290px; top: 52px; }
  .contact__name { font-size: 30px; font-weight: 900; color: var(--red); line-height: 1; }
  .contact__title { font-size: 12.5px; font-weight: 500; margin-top: 4px; }
  .contact__company { font-size: 12.5px; font-weight: 500; margin-top: 22px; }
  .contact__list { list-style: none; margin-top: 16px; font-size: 12.5px; font-weight: 500; }
  .contact__list li { display: flex; align-items: center; gap: 8px; margin-bottom: 6px; }
  .icon { width: 13px; height: 13px; flex: none; }
  .bands { position: absolute; left: 0; top: 0; width: 560px; height: 320px; }
</style>
</head>
<body>

<section class="card card--back">
  <div class="brand"><span class="brand__dot"></span>Harborline Builders</div>
  <p class="guarantee">OUR SERVICES ARE 100% GUARANTEED</p>
  <p class="specialty"><span class="specialty__rule"></span>SPECIALIZING IN:<span class="specialty__rule"></span></p>
  <ul class="services">
    <li><svg class="tick" viewBox="0 0 10 10"><circle cx="5" cy="5" r="4.2" fill="none" stroke="#ed1c24"/><path d="M3 5.2l1.4 1.4L7.2 3.6" fill="none" stroke="#ed1c24" stroke-width="1.2"/></svg>Remodel: Kitchen &amp; Bath</li>
    <li><svg class="tick" viewBox="0 0 10 10"><circle cx="5" cy="5" r="4.2" fill="none" stroke="#ed1c24"/><path d="M3 5.2l1.4 1.4L7.2 3.6" fill="none" stroke="#ed1c24" stroke-width="1.2"/></svg>Painting: Interior &amp; Exterior</li>
    <li><svg class="tick" viewBox="0 0 10 10"><circle cx="5" cy="5" r="4.2" fill="none" stroke="#ed1c24"/><path d="M3 5.2l1.4 1.4L7.2 3.6" fill="none" stroke="#ed1c24" stroke-width="1.2"/></svg>Flooring: Carpet, Vinyl, Wood</li>
    <li><svg class="tick" viewBox="0 0 10 10"><circle cx="5" cy="5" r="4.2" fill="none" stroke="#ed1c24"/><path d="M3 5.2l1.4 1.4L7.2 3.6" fill="none" stroke="#ed1c24" stroke-width="1.2"/></svg>Window &amp; Door Replacement</li>
    <li><svg class="tick" viewBox="0 0 10 10"><circle cx="5" cy="5" r="4.2" fill="none" stroke="#ed1c24"/><path d="M3 5.2l1.4 1.4L7.2 3.6" fill="none" stroke="#ed1c24" stroke-width="1.2"/></svg>Plumbing: Repairs &amp; Upgrades</li>
    <li><svg class="tick" viewBox="0 0 10 10"><circle cx="5" cy="5" r="4.2" fill="none" stroke="#ed1c24"/><path d="M3 5.2l1.4 1.4L7.2 3.6" fill="none" stroke="#ed1c24" stroke-width="1.2"/></svg>Energy-Efficient Upgrades</li>
    <li><svg class="tick" viewBox="0 0 10 10"><circle cx="5" cy="5" r="4.2" fill="none" stroke="#ed1c24"/><path d="M3 5.2l1.4 1.4L7.2 3.6" fill="none" stroke="#ed1c24" stroke-width="1.2"/></svg>Deck &amp; Patio Construction</li>
    <li><svg class="tick" viewBox="0 0 10 10"><circle cx="5" cy="5" r="4.2" fill="none" stroke="#ed1c24"/><path d="M3 5.2l1.4 1.4L7.2 3.6" fill="none" stroke="#ed1c24" stroke-width="1.2"/></svg>Water &amp; Mold Damage</li>
    <li><svg class="tick" viewBox="0 0 10 10"><circle cx="5" cy="5" r="4.2" fill="none" stroke="#ed1c24"/><path d="M3 5.2l1.4 1.4L7.2 3.6" fill="none" stroke="#ed1c24" stroke-width="1.2"/></svg>Garage Renovation</li>
  </ul>
</section>

<section class="card card--front">
  <svg class="bands" viewBox="0 0 560 320" aria-hidden="true">
    <polygon points="0,292 320,256 345,256 0,308" fill="var(--red)"/>
    <polygon points="330,258 560,214 560,232 370,266 340,264" fill="var(--blue)"/>
  </svg>
  <div class="brand"><span class="brand__dot"></span>Harborline Builders</div>
  <span class="divider"></span>
  <div class="contact">
    <h1 class="contact__name">Marcus Delling</h1>
    <p class="contact__title">Licensed General Contractors</p>
    <p class="contact__company">Harborline Builders Inc.</p>
    <ul class="contact__list">
      <li><svg class="icon" viewBox="0 0 14 14"><path d="M3 1.5l2.3 2.6-1.2 1.5c.8 1.7 2.2 3.1 3.9 3.9l1.5-1.2 2.6 2.3-1.3 1.9C6 12.3 1.7 8 1.2 2.8z" fill="var(--red)"/></svg>858-471-6093</li>
      <li><svg class="icon" viewBox="0 0 14 14"><rect x="1" y="3" width="12" height="8.5" rx="1" fill="var(--red)"/><path d="M1.5 3.6L7 8l5.5-4.4" fill="none" stroke="#1e1f24" stroke-width="1.2"/></svg>info@brightoakbuilders.com</li>
      <li><svg class="icon" viewBox="0 0 14 14"><circle cx="7" cy="7" r="5.8" fill="var(--red)"/><path d="M1.2 7h11.6M7 1.2c-2.4 3-2.4 8.6 0 11.6M7 1.2c2.4 3 2.4 8.6 0 11.6" fill="none" stroke="#1e1f24" stroke-width="0.9"/></svg>www.brightoakbuilders.com</li>
    </ul>
  </div>
</section>

</body>
</html>
```